High-end construction company needs a business card design

We need a modern looking business card that draws people in, is memorable and looks so good people will want to sick it on their fridges.
On the first side what is needed are:
Logo
My name - Tomasz Brelwik
Title - Managing Director
Website - www.varkelt.co.uk
Email - tomasz@varkelt.co.uk
Telephone - 020 5194 6281
Mobile - 07845139072
On the back side was is needed is a list of all the services we provide:
-Kitchen Renovations
-Bathroom Renovations
-House Renovations
-Garage Conversions
-Extensions
-Loft Conversions
-Conservatories
-Carpentry
-Tiling
-Electrical
-Plumbing & Heating
-Bricklaying
-Landscaping
-Decorating
-Plastering
We would like the colours to be the same shades as on the logo with grey or black for the words.
Target Market(s)
Anyone who needs building work done
Contact Information for Business Card
This business card is for a construction company which strives to deliver excellent service and quality.
The look and feel of the card should represent this.
Requirements
Must have
- On the first side what is needed are:
Logo
My name - Tomasz Brelwik
Title - Managing Director
Website - www.varkelt.co.uk
Email - tomasz@varkelt.co.uk
Telephone - 020 5194 6281
Mobile - 07845139072
Nice to have
- Cool looking features

```html
<!DOCTYPE html>
<html lang="en">
<head>
<meta charset="utf-8">
<title>Varkelt Construction Ltd – Business Card</title>
<link href="https://fonts.googleapis.com/css2?family=Montserrat:wght@400;500;700;800&display=swap" rel="stylesheet">
<style>
  :root {
    --stage: #e4e4e4;
    --green: #6db73f;
    --green-dark: #3d8a2c;
    --green-soft: rgba(255,255,255,0.12);
    --paper: #f4f4f4;
    --white: #ffffff;
  }
  * { margin: 0; padding: 0; box-sizing: border-box; }
  html, body { width: 1200px; height: 960px; overflow: hidden; }
  body {
    background: var(--stage);
    font-family: "Montserrat", sans-serif;
    position: relative;
  }
  .card {
    position: absolute;
    left: 325px;
    width: 552px;
    height: 358px;
    overflow: hidden;
  }
  /* Services side */
  .card--services { top: 104px; background: var(--green); }
  .decor-machinery {
    position: absolute;
    left: 0; top: 0; width: 552px; height: 358px;
    background:
      radial-gradient(ellipse 260px 200px at 420px 200px, var(--green-soft), transparent 70%),
      linear-gradient(160deg, transparent 40%, rgba(255,255,255,0.08) 70%, transparent 95%);
  }
  .brand {
    position: absolute;
    font-family: "Montserrat", sans-serif;
    font-weight: 800;
    line-height: 1;
    text-transform: uppercase;
  }
  .brand__name { display: block; font-size: 44px; letter-spacing: 1px; }
  .brand__sub { display: block; font-size: 13.5px; letter-spacing: 2.2px; margin-top: 6px; }
  .card--services .brand { left: 45px; top: 195px; color: var(--white); }
  .services {
    position: absolute;
    left: 328px; top: 31px;
    list-style: none;
    color: var(--white);
    font-size: 15px;
    line-height: 19.6px;
    font-weight: 400;
    letter-spacing: 0.2px;
  }
  .services li::before { content: "•"; margin-right: 6px; }

  /* Contact side */
  .card--contact { top: 504px; background: var(--paper); }
  .card--contact .diagonal { position: absolute; inset: 0; }
  .card--contact .brand { left: 42px; top: 118px; color: var(--green); }
  .contact {
    position: absolute;
    right: 34px; top: 172px;
    text-align: right;
    color: var(--white);
  }
  .contact__name { font-size: 17px; font-weight: 700; letter-spacing: 0.6px; text-transform: uppercase; }
  .contact__title { font-size: 15px; font-weight: 400; margin-top: 2px; }
  .contact__lines { list-style: none; margin-top: 30px; font-size: 14px; line-height: 19.5px; }
  .contact__lines li { display: flex; justify-content: flex-end; align-items: center; gap: 6px; }
  .contact__lines svg { width: 12px; height: 12px; flex: none; }
</style>
</head>
<body>

<section class="card card--services">
  <div class="decor-machinery" role="img" aria-label="Faint illustration of an excavator arm over house roofs and buildings"></div>
  <div class="brand">
    <span class="brand__name">Varkelt</span>
    <span class="brand__sub">Construction Ltd</span>
  </div>
  <ul class="services">
    <li>Kitchen Renovations</li>
    <li>Bathroom Renovations</li>
    <li>House Renovations</li>
    <li>Garage Conversions</li>
    <li>Plumbing &amp; Heating</li>
    <li>Loft Conversions</li>
    <li>Conservatories</li>
    <li>Extensions</li>
    <li>Carpentry</li>
    <li>Electrical</li>
    <li>Bricklaying</li>
    <li>Landscaping</li>
    <li>Decorating</li>
    <li>Plastering</li>
    <li>Tiling</li>
  </ul>
</section>

<section class="card card--contact">
  <svg class="diagonal" viewBox="0 0 552 358" width="552" height="358" aria-hidden="true">
    <polygon points="412,0 552,0 552,358 157,358" fill="var(--green)"/>
    <line x1="412" y1="0" x2="157" y2="358" stroke="var(--green-dark)" stroke-width="5"/>
  </svg>
  <div class="brand">
    <span class="brand__name">Varkelt</span>
    <span class="brand__sub">Construction Ltd</span>
  </div>
  <div class="contact">
    <p class="contact__name">Tomasz Brelwik</p>
    <p class="contact__title">Managing Director</p>
    <ul class="contact__lines">
      <li>020 5194 6281
        <svg viewBox="0 0 24 24"><path fill="#fff" d="M6.6 10.8a15 15 0 0 0 6.6 6.6l2.2-2.2a1 1 0 0 1 1-.25 11.4 11.4 0 0 0 3.6.57 1 1 0 0 1 1 1V20a1 1 0 0 1-1 1A17 17 0 0 1 3 4a1 1 0 0 1 1-1h3.5a1 1 0 0 1 1 1c0 1.25.2 2.45.57 3.57a1 1 0 0 1-.25 1z"/></svg>
      </li>
      <li>07845139072
        <svg viewBox="0 0 24 24"><rect x="6" y="2" width="12" height="20" rx="2" fill="none" stroke="#fff" stroke-width="2"/><circle cx="12" cy="18" r="1.2" fill="#fff"/></svg>
      </li>
      <li>tomasz@varkelt.co.uk
        <svg viewBox="0 0 24 24"><rect x="2" y="5" width="20" height="14" fill="none" stroke="#fff" stroke-width="2"/><path d="M2 5l10 8 10-8" fill="none" stroke="#fff" stroke-width="2"/></svg>
      </li>
      <li>www.varkelt.co.uk
        <svg viewBox="0 0 24 24"><circle cx="12" cy="12" r="9.5" fill="none" stroke="#fff" stroke-width="2"/><ellipse cx="12" cy="12" rx="4" ry="9.5" fill="none" stroke="#fff" stroke-width="1.6"/><path d="M2.5 12h19M4 7h16M4 17h16" stroke="#fff" stroke-width="1.4"/></svg>
      </li>
    </ul>
  </div>
</section>

</body>
</html>
```